business card - Helicopter Flight Services, Flight School, etc.

We need a business card design for a new helicopter service.

We offer Helicopter Flight Services, Aerial Filming & Photography, Flight School, and Helicopter Tours. In that order.

Summit BladeAir, Inc.
Dennis Tollerby
SummitBladeair@Kestmail.com
626-418-7352

Based at the Brenwick Airport in Van Nuys, CA. The final design should communicate integrity and safety. Pictures or logos at your discretion.

Card back side - surprise me.

```html
<!DOCTYPE html>
<html lang="en">
<head>
<meta charset="utf-8">
<title>Summit BladeAir, Inc. – Business Card</title>
<link rel="stylesheet" href="https://fonts.googleapis.com/css2?family=Open+Sans:wght@400;600&display=swap">
<style>
  :root {
    --page: #e6e4e0;
    --card-white: #ffffff;
    --card-black: #0b0b0b;
    --card-black-hi: #262626;
    --ink: #111111;
    --ink-soft: #2b2b2b;
    --paper-text: #f4f4f4;
    --ornament: #3a3a3a;
  }
  * { box-sizing: border-box; margin: 0; padding: 0; }
  html, body {
    width: 1200px; height: 892px; overflow: hidden;
    background: var(--page);
    font-family: "Open Sans", sans-serif;
  }
  .canvas {
    position: relative; width: 1200px; height: 892px;
  }
  .card {
    position: absolute; left: 320px; width: 560px; height: 320px;
    box-shadow: 0 6px 18px rgba(0,0,0,0.18);
  }
  /* Front */
  .card-front { top: 100px; background: var(--card-white); color: var(--ink); }
  .corner-frame { position: absolute; }
  .corner-frame.top-left { left: 18px; top: 18px; }
  .corner-frame.bottom-right { right: 18px; bottom: 18px; transform: rotate(180deg); }
  .company-name {
    position: absolute; left: 46px; top: 52px;
    font-size: 22px; font-weight: 400; letter-spacing: 0.2px;
  }
  .divider { position: absolute; left: 262px; top: 70px; }
  .person-name {
    position: absolute; left: 290px; top: 150px;
    font-size: 23px; font-weight: 400;
  }
  .contact-list {
    position: absolute; left: 272px; top: 192px;
    list-style: none; font-size: 12.5px; line-height: 18px; color: var(--ink-soft);
  }
  .contact-list li { display: flex; align-items: flex-start; gap: 7px; }
  .contact-icon { flex: 0 0 12px; margin-top: 3px; }
  .contact-list .address-line { padding-left: 19px; }
  /* Back */
  .card-back {
    top: 472px;
    background: linear-gradient(160deg, var(--card-black-hi) 0%, var(--card-black) 45%, var(--card-black) 100%);
    color: var(--paper-text);
    display: flex; flex-direction: column; align-items: center; justify-content: center;
  }
  .back-brand { font-size: 50px; font-weight: 400; letter-spacing: 0.5px; line-height: 1.1; }
  .back-services { margin-top: 10px; font-size: 22px; font-weight: 400; letter-spacing: 0.3px; }
</style>
</head>
<body>
<main class="canvas">

  <section class="card card-front" aria-label="Card front">
    <svg class="corner-frame top-left" width="220" height="110" viewBox="0 0 220 110">
      <line x1="4" y1="4" x2="216" y2="4" stroke="var(--ornament)" stroke-width="1"/>
      <line x1="4" y1="4" x2="4" y2="106" stroke="var(--ornament)" stroke-width="1"/>
      <circle cx="216" cy="4" r="2" fill="var(--ornament)"/>
      <circle cx="4" cy="106" r="2" fill="var(--ornament)"/>
      <rect x="0" y="0" width="34" height="26" fill="var(--ornament)" opacity="0.35" role="img" aria-label="Corner scroll ornament"/>
    </svg>

    <div class="company-name">Summit BladeAir, Inc.</div>

    <svg class="divider" width="20" height="200" viewBox="0 0 20 200">
      <line x1="10" y1="0" x2="10" y2="200" stroke="var(--ornament)" stroke-width="1"/>
      <rect x="4" y="86" width="12" height="12" fill="var(--ornament)" transform="rotate(45 10 92)" role="img" aria-label="Divider ornament"/>
    </svg>

    <div class="person-name">Dennis Tollerby</div>

    <ul class="contact-list">
      <li>
        <svg class="contact-icon" width="12" height="12" viewBox="0 0 12 12" aria-hidden="true">
          <rect width="12" height="12" fill="var(--ink)"/>
          <path d="M3.5 2.5 L5 4.5 L4.3 5.3 Q5.3 7 6.8 7.8 L7.6 7 L9.5 8.5 L8.6 9.6 Q5 9 2.6 3.4 Z" fill="#fff"/>
        </svg>
        <span>626-418-7352</span>
      </li>
      <li>
        <svg class="contact-icon" width="12" height="12" viewBox="0 0 12 12" aria-hidden="true">
          <rect width="12" height="12" fill="var(--ink)"/>
          <rect x="2.5" y="3.5" width="7" height="5" fill="none" stroke="#fff" stroke-width="1"/>
          <path d="M2.5 3.5 L6 6.5 L9.5 3.5" fill="none" stroke="#fff" stroke-width="1"/>
        </svg>
        <span>SummitBladeair@Kestmail.com</span>
      </li>
      <li>
        <svg class="contact-icon" width="12" height="12" viewBox="0 0 12 12" aria-hidden="true">
          <rect width="12" height="12" fill="var(--ink)"/>
          <path d="M6 10 Q2.8 6.4 2.8 4.8 A3.2 3.2 0 0 1 9.2 4.8 Q9.2 6.4 6 10 Z" fill="#fff"/>
          <circle cx="6" cy="4.8" r="1.2" fill="var(--ink)"/>
        </svg>
        <span>2740 W. Larchmont Ave. Ste.A</span>
      </li>
      <li class="address-line">Halvern, CA 90417</li>
    </ul>

    <svg class="corner-frame bottom-right" width="220" height="110" viewBox="0 0 220 110">
      <line x1="4" y1="4" x2="216" y2="4" stroke="var(--ornament)" stroke-width="1"/>
      <line x1="4" y1="4" x2="4" y2="106" stroke="var(--ornament)" stroke-width="1"/>
      <circle cx="216" cy="4" r="2" fill="var(--ornament)"/>
      <circle cx="4" cy="106" r="2" fill="var(--ornament)"/>
      <rect x="0" y="0" width="34" height="26" fill="var(--ornament)" opacity="0.35" role="img" aria-label="Corner scroll ornament"/>
    </svg>
  </section>

  <section class="card card-back" aria-label="Card back">
    <div class="back-brand">Summit BladeAir</div>
    <div class="back-services">Airport · Tour guide · Heliport</div>
  </section>

</main>
</body>
</html>
```